UI/ UX Design for ERP Software

We need a new UX/UI interface for a ERP software for property managers. Our CMMS / ERP solution is made based on responsive design technologies and is coded in PHP.
The overall UX to be similar to Tev Ulna - easy navigation, intuitive menus.

Industry/Entity Type

Property Management

Number of Pages Required

5+ page

Requirements
Must have
• Round dock buttons
Consistent icons across the application
Enough Spacing between buttons/icons/ menu
Consistent Font
Nice to have
• We would like the UX to allow the users to use the application without /minimum training.
Should not have
• we don't want anything that is classic with respect to UX

```html
<!DOCTYPE html>
<html lang="en">
<head>
<meta charset="utf-8">
<title>Estora – Active Dashboard</title>
<link href="https://fonts.googleapis.com/css2?family=Lato:wght@400;700;900&display=swap" rel="stylesheet">
<style>
:root{
  --blue:#0a7cff;
  --blue-deep:#0c5fe0;
  --cyan:#12c6f5;
  --band:#c6e9f8;
  --ink:#4a5568;
  --slate:#4f6075;
  --grid:#e3e6ea;
  --page:#f5f5f5;
  --white:#ffffff;
}
*{box-sizing:border-box;margin:0;padding:0}
html,body{width:1200px;height:1064px;overflow:hidden}
body{position:relative;background:var(--page);font-family:'Lato',sans-serif;color:var(--ink)}
.brand{position:absolute;left:0;top:0;width:207px;height:146px;background:var(--white)}
.brand-name{position:absolute;left:30px;top:42px;display:flex;align-items:center;gap:8px;font-size:34px;font-weight:900;color:var(--blue)}
.brand-name .dot{width:22px;height:22px;border-radius:50%;background:var(--blue)}
.brand-curve{position:absolute;left:0;top:110px}
.nav{position:absolute;left:207px;top:0;width:993px;height:50px;background:linear-gradient(90deg,#0b8ef5,#0b5ef4 60%,#1a4ef0);display:flex;align-items:center;font-size:12.5px;color:var(--white)}
.nav a{color:inherit;text-decoration:none;margin-right:20px;white-space:nowrap}
.nav .active{background:var(--cyan);height:50px;width:117px;display:flex;align-items:center;justify-content:center;margin-right:18px}
.stats{position:absolute;left:207px;top:50px;width:993px;height:96px;background:var(--band);display:flex;align-items:center;padding-left:44px}
.stat{display:flex;align-items:center;gap:12px}
.stat .ico{width:40px;height:40px;border-radius:50%;border:3px solid var(--blue);background:var(--white);display:flex;align-items:center;justify-content:center}
.stat b{display:block;font-size:18px;font-weight:700;color:var(--ink);line-height:1.1}
.stat span{font-size:14.5px;color:var(--ink)}
.card{position:absolute;left:32px;top:176px;width:1137px;height:806px;background:var(--white)}
.title{position:absolute;left:30px;top:28px;font-size:37px;font-weight:900;color:var(--slate)}
.title em{font-style:normal;color:var(--blue)}
.ranges{position:absolute;left:579px;top:32px;display:flex;gap:8px}
.ranges span{width:80px;height:29px;border:1px solid #cfd4da;font-size:10.5px;display:flex;align-items:center;justify-content:center;color:var(--ink)}
.ranges .on{background:var(--blue);border-color:var(--blue);color:var(--white)}
.period{position:absolute;left:30px;top:110px;width:264px;height:39px;background:var(--slate);color:var(--white);font-size:18px;font-weight:700;display:flex;align-items:center;gap:8px;padding-left:17px}
.chart{position:absolute;left:0;top:0}
.legend{position:absolute;left:119px;top:719px;font-size:12px;color:var(--ink);line-height:29px;width:760px}
.legend i{display:inline-block;width:10px;height:10px;border-radius:2px;margin:0 6px 0 2px;vertical-align:-1px}
.legend span{margin-right:6px;white-space:nowrap}
.footer{position:absolute;left:0;top:1011px;width:1200px;height:53px;background:var(--slate);color:var(--white);font-size:12.5px;display:flex;align-items:center;justify-content:center}
.footer .code{position:absolute;right:34px}
</style>
</head>
<body>
<div class="brand">
  <div class="brand-name"><span class="dot"></span>Estora</div>
  <svg class="brand-curve" width="207" height="36" viewBox="0 0 207 36"><path d="M0 36 Q100 -12 207 36" fill="none" stroke="#4f6075" stroke-width="5"/></svg>
</div>
<nav class="nav">
  <a class="active" href="#">Dashboard</a><a href="#">Customers</a><a href="#">Properties</a><a href="#">Tenants</a><a href="#">Contacts</a><a href="#">Contractors</a><a href="#">Employees</a><a href="#">Compilance Management</a><a href="#">Prevent.Maintenance</a><a href="#">More</a>
</nav>
<section class="stats">
  <div class="stat" style="margin-right:30px"><div class="ico"><svg width="18" height="16" viewBox="0 0 18 16"><path d="M9 1 L17 8 H14 V15 H11 V10 H7 V15 H4 V8 H1 Z" fill="#0a7cff"/></svg></div><div><b>03</b><span>Properties</span></div></div>
  <div class="stat" style="margin-right:30px"><div class="ico"><svg width="20" height="16" viewBox="0 0 20 16"><circle cx="10" cy="4" r="3" fill="#0a7cff"/><circle cx="4" cy="5" r="2.3" fill="#0a7cff"/><circle cx="16" cy="5" r="2.3" fill="#0a7cff"/><path d="M4 15 Q4 8 10 8 Q16 8 16 15Z M0 13 Q0 8 4 8 L3 13Z M20 13 Q20 8 16 8 L17 13Z" fill="#0a7cff"/></svg></div><div><b>08</b><span>Tenants</span></div></div>
  <div class="stat" style="margin-right:30px"><div class="ico"><svg width="20" height="20" viewBox="0 0 20 20"><path d="M10 1 L13 4 H11 V9 H16 V7 L19 10 L16 13 V11 H11 V16 H13 L10 19 L7 16 H9 V11 H4 V13 L1 10 L4 7 V9 H9 V4 H7Z" fill="#0a7cff"/></svg></div><div><b>422,000.00sq.ft</b><span>Total Properties Area</span></div></div>
  <div class="stat" style="margin-right:30px"><div class="ico"><svg width="18" height="18" viewBox="0 0 18 18"><path d="M1 1 H7 L5 3 L9 7 L13 3 L11 1 H17 V7 L15 5 L11 9 L15 13 L17 11 V17 H11 L13 15 L9 11 L5 15 L7 17 H1 V11 L3 13 L7 9 L3 5 L1 7Z" fill="#0a7cff"/></svg></div><div><b>233,500.00sq.ft</b><span>Rented Area</span></div></div>
  <div class="stat"><div class="ico"><svg width="20" height="20" viewBox="0 0 20 20"><path d="M10 1 L13 4 H11 V9 H16 V7 L19 10 L16 13 V11 H11 V16 H13 L10 19 L7 16 H9 V11 H4 V13 L1 10 L4 7 V9 H9 V4 H7Z" fill="#0a7cff"/></svg></div><div><b>188,500.00sq.ft</b><span>Vacancies Area</span></div></div>
</section>
<main class="card">
  <h1 class="title">Active <em>Dashboard</em></h1>
  <div class="ranges"><span class="on">Last 7 Days</span><span>Last Months</span><span>Last 3 Months</span><span>Next 7 Days</span><span>Next Months</span><span>Mext 3 Months</span></div>
  <div class="period"><svg width="18" height="14" viewBox="0 0 18 14"><path d="M1 0 V13 H17" fill="none" stroke="#fff" stroke-width="1.5"/><rect x="4" y="6" width="2" height="6" fill="#fff"/><rect x="8" y="3" width="2" height="9" fill="#fff"/><rect x="12" y="7" width="2" height="5" fill="#fff"/></svg>12/27/2020 - 01/03/2021</div>
  <div class="legend">
    <span><i style="background:#0a7cff"></i>Scheduled Maintenance</span>
    <span><i style="background:#5ccf3c"></i>Completed Scheduled Maintenance</span>
    <span><i style="background:#f2c94c"></i>Future Scheduled Maintenance</span>
    <span><i style="background:#4f6075"></i>Scheduled Work Orders</span><br>
    <span><i style="background:#a66be8"></i>Completed Work Orders</span>
    <span><i style="background:#f06bb5"></i>Property Inspections in Progress</span>
    <span><i style="background:#e0b04a"></i>Completed Property Inspections</span>
  </div>
</main>
<svg class="chart" width="1200" height="1064" viewBox="0 0 1200 1064" font-family="Lato, sans-serif" font-size="12.5" fill="#4a5568">
  <g stroke="#e3e6ea" stroke-width="1">
    <line x1="142" y1="382" x2="1098" y2="382"/><line x1="142" y1="465" x2="1098" y2="465"/>
    <line x1="142" y1="548" x2="1098" y2="548"/><line x1="142" y1="631" x2="1098" y2="631"/>
    <line x1="142" y1="713" x2="1098" y2="713"/><line x1="142" y1="798" x2="1098" y2="798"/>
    <line x1="142" y1="363" x2="142" y2="798" stroke="#cfd4da"/>
  </g>
  <g><text x="93" y="387">1.25</text><text x="93" y="470">1</text><text x="93" y="552">0.75</text><text x="93" y="635">0.5</text><text x="93" y="717">0.25</text><text x="93" y="799">0</text></g>
  <g fill="#4a5568"><rect x="57" y="378" width="13" height="2"/><rect x="57" y="382" width="13" height="2"/><rect x="57" y="386" width="13" height="2"/></g>
  <text transform="translate(68 608) rotate(-90)" font-size="12" font-weight="700" text-anchor="middle">NUMBER</text>
  <g fill="#0a7cff">
    <rect x="423" y="710" width="13" height="89"/><rect x="549" y="630" width="13" height="169"/>
    <rect x="675" y="648" width="13" height="151"/><rect x="802" y="682" width="13" height="117"/>
    <rect x="928" y="746" width="13" height="53"/><rect x="1055" y="771" width="13" height="28"/>
  </g>
  <g fill="#fff" stroke="#0a7cff" stroke-width="3">
    <circle cx="430" cy="710" r="9.5"/><circle cx="556" cy="630" r="9.5"/><circle cx="682" cy="648" r="9.5"/>
    <circle cx="809" cy="682" r="9.5"/><circle cx="935" cy="746" r="9.5"/><circle cx="1062" cy="771" r="9.5"/>
  </g>
  <g text-anchor="middle">
    <text x="177" y="837">12/27/20</text><text x="303" y="837">12/28/20</text><text x="430" y="837">12/29/20</text>
    <text x="556" y="837">12/30/20</text><text x="682" y="837">12/31/20</text><text x="809" y="837">01/01/21</text>
    <text x="935" y="837">02/01/21</text><text x="1062" y="837">03/01/21</text>
  </g>
</svg>
<footer class="footer">© 2021 ERP software. All rights reserved.Privacy Terms of Use<span class="code">C9</span></footer>
</body>
</html>
```